Home Staging Company needs business card design

We're a home staging company called Brightly Settled Home Staging. We would like a business card design that includes aqua and gray. Our current logo of house within chair is fine but I find we almost always use the logo in one color. I'll upload images of front and back of our current card and our logo. Note that we have dropped "Solutions" from our company name and don't want to include it on the card.

Target Market(s)

Realtors and homeowners - people interested in selling their homes

Contact Information for Business Card

Marisol Thistlewood
Brightly Settled Home Staging
757-555-0193
www.brightlysettled.com
marisol@brightlysettled.com

Font styles to use
Serif
Script

Requirements
Must have
• My logo and contact details
• UPDATE***
• I forgot to say that the company name should be included on the front of the card somehow.

```html
<!DOCTYPE html>
<html lang="en">
<head>
<meta charset="utf-8">
<title>Brightly Settled Home Staging – Business Card</title>
<link href="https://fonts.googleapis.com/css2?family=Questrial&family=Roboto:wght@400&display=swap" rel="stylesheet">
<style>
  :root {
    --backdrop: #3a3a3a;
    --card-black: #1f1f20;
    --card-white: #fbfbfb;
    --band-gray: #3b3e40;
    --aqua: #5bbcc6;
    --ink-white: #f2f2f2;
    --ink-gray: #c9c9c9;
    --ink-dark: #2b2b2b;
    --emboss: #2c2c2d;
  }
  html, body {
    margin: 0;
    padding: 0;
    width: 799px;
    height: 1200px;
    overflow: hidden;
    background: var(--backdrop);
    font-family: "Questrial", sans-serif;
  }
  .canvas {
    position: relative;
    width: 799px;
    height: 1200px;
  }
  .card {
    position: absolute;
    left: 80px;
    width: 640px;
    height: 366px;
    background: var(--card-black);
    box-shadow: 0 14px 30px rgba(0,0,0,0.45);
    overflow: hidden;
  }
  .card--front { top: 150px; }
  .card--back { top: 690px; }

  /* Front */
  .front-mark {
    position: absolute;
    inset: 0;
    display: flex;
    flex-direction: column;
    align-items: center;
    justify-content: center;
    gap: 22px;
  }
  .front-mark__circle {
    width: 150px;
    height: 150px;
    border-radius: 50%;
    background: var(--emboss);
  }
  .front-mark__name {
    font-family: "Questrial", sans-serif;
    font-size: 22px;
    letter-spacing: 1px;
    color: #5a5a5c;
  }

  /* Back */
  .back-shape {
    position: absolute;
    inset: 0;
  }
  .holder {
    position: absolute;
    left: 34px;
    top: 34px;
  }
  .holder__name {
    font-family: "Roboto", sans-serif;
    font-size: 21px;
    color: var(--ink-white);
    margin: 0;
  }
  .holder__surname { color: var(--aqua); }
  .holder__title {
    font-size: 11px;
    color: var(--ink-gray);
    margin: 4px 0 0;
  }
  .contacts {
    position: absolute;
    left: 34px;
    bottom: 58px;
    margin: 0;
    padding: 0;
    list-style: none;
  }
  .contacts__item {
    display: flex;
    align-items: center;
    gap: 12px;
    font-size: 15px;
    color: var(--ink-white);
    line-height: 22px;
  }
  .contacts__icon {
    width: 12px;
    height: 12px;
    fill: var(--aqua);
    flex: none;
  }
  .brand {
    position: absolute;
    right: 30px;
    top: 0;
    bottom: 0;
    width: 220px;
    display: flex;
    flex-direction: column;
    align-items: center;
    justify-content: center;
    gap: 16px;
  }
  .brand__circle {
    width: 80px;
    height: 80px;
    border-radius: 50%;
    background: var(--aqua);
  }
  .brand__name {
    font-family: "Questrial", sans-serif;
    font-size: 19px;
    line-height: 1.3;
    color: var(--ink-dark);
    text-align: center;
  }
</style>
</head>
<body>
<div class="canvas">

  <section class="card card--front" aria-label="Card front">
    <div class="front-mark">
      <div class="front-mark__circle"></div>
      <div class="front-mark__name">Brightly Settled Home Staging</div>
    </div>
  </section>

  <section class="card card--back" aria-label="Card back">
    <svg class="back-shape" width="640" height="366" viewBox="0 0 640 366" aria-hidden="true">
      <path d="M476 0 Q392 150 384 366 L640 366 L640 0 Z" fill="var(--band-gray)"/>
      <path d="M490 0 Q406 150 398 366 L640 366 L640 0 Z" fill="var(--card-white)"/>
    </svg>

    <div class="holder">
      <p class="holder__name">Marisol <span class="holder__surname">Thistlewood</span></p>
      <p class="holder__title">Managing Director</p>
    </div>

    <ul class="contacts">
      <li class="contacts__item">
        <svg class="contacts__icon" viewBox="0 0 24 24"><path d="M6.6 10.8a15 15 0 0 0 6.6 6.6l2.2-2.2a1 1 0 0 1 1-.25 11.4 11.4 0 0 0 3.6.57 1 1 0 0 1 1 1V20a1 1 0 0 1-1 1A17 17 0 0 1 3 4a1 1 0 0 1 1-1h3.5a1 1 0 0 1 1 1c0 1.25.2 2.45.57 3.57a1 1 0 0 1-.25 1z"/></svg>
        757-555-0193
      </li>
      <li class="contacts__item">
        <svg class="contacts__icon" viewBox="0 0 24 24"><path d="M12 2a10 10 0 1 0 0 20 10 10 0 0 0 0-20zm6.9 6h-2.9a15.7 15.7 0 0 0-1.4-3.6A8 8 0 0 1 18.9 8zM12 4c.8 1.2 1.5 2.5 1.9 4h-3.8c.4-1.5 1.1-2.8 1.9-4zM4.3 14a8 8 0 0 1 0-4h3.4a16 16 0 0 0 0 4zm.8 2h2.9c.3 1.3.8 2.5 1.4 3.6A8 8 0 0 1 5.1 16zM8 8H5.1a8 8 0 0 1 4.3-3.6C8.8 5.5 8.3 6.7 8 8zm4 12c-.8-1.2-1.5-2.5-1.9-4h3.8c-.4 1.5-1.1 2.8-1.9 4zm2.3-6H9.7a14.7 14.7 0 0 1 0-4h4.6a14.7 14.7 0 0 1 0 4zm.3 5.6c.6-1.1 1.1-2.3 1.4-3.6h2.9a8 8 0 0 1-4.3 3.6zM16.3 14a16 16 0 0 0 0-4h3.4a8 8 0 0 1 0 4z"/></svg>
        www.brightlysettled.com
      </li>
      <li class="contacts__item">
        <svg class="contacts__icon" viewBox="0 0 24 24"><path d="M2 5h20v14H2zm2 2v.5l8 5 8-5V7zm0 2.8V17h16V9.8l-8 5z"/></svg>
        marisol@brightlysettled.com
      </li>
    </ul>

    <div class="brand">
      <div class="brand__circle"></div>
      <div class="brand__name">Brightly Settled<br>Home Staging</div>
    </div>
  </section>

</div>
</body>
</html>
```